Creative Web design for Tattoo Artist

I am a tattoo artist with a private tattoo/art studio in Spring, TX. I need to design a website for my studio, to include the following "pages" :
-home/about
-FAQ
-Gallery
-Inquiries
-shop
We would like to see designs that are more dark or "moody", and like the colors black/gold.
I'd like my website to reflect my studio, an award winning private, upscale custom only tattoo studio.

I've attached some examples of styles we liked.

Target Market(s)

adults ages 18-50, interested in tattoos, or fine art

Industry/Entity Type

Tattoos/Fine Art/Arts

Coding

Coded - Design and coding required

Number of Pages Required

5+ page

Colors

Designer to choose colors to be used in the design.

Requirements
Must have
• gallery section, and e-commerce page set up so I can begin selling merchandise, I'd like the fonts to flow with my logo design

```html
<!DOCTYPE html>
<html lang="en">
<head>
<meta charset="utf-8">
<title>The Gilded Viper — Tattoo &amp; Art Studio</title>
<link href="https://fonts.googleapis.com/css2?family=Bitter:wght@400;500;600;700&family=Josefin+Sans:wght@300;400;600&family=Roboto:wght@400;500&display=swap" rel="stylesheet">
<style>
:root{
  --gold:#d9a41c;
  --gold-deep:#c8930f;
  --black:#000;
  --coal:#0b0b0b;
  --ink:#141414;
  --white:#fff;
  --text:#e6e6e6;
  --dark-text:#1d1d1d;
}
*{margin:0;padding:0;box-sizing:border-box}
html,body{width:1200px;height:4370px;overflow:hidden;background:var(--black)}
body{position:relative;font-family:"Josefin Sans",sans-serif;color:var(--text)}
.section{position:absolute;left:0;width:1200px;overflow:hidden}
.abs{position:absolute}
.heading{font-family:"Bitter",serif;font-weight:600;color:var(--gold);text-transform:uppercase;letter-spacing:1px}
.btn{position:absolute;background:var(--gold);color:var(--dark-text);font-family:"Bitter",serif;font-weight:500;font-size:25px;display:flex;align-items:center;justify-content:center}
.frame{position:absolute;border:2px solid var(--gold)}
.photo{position:absolute}
.para{position:absolute;font-size:15.2px;line-height:27.5px;font-weight:300;color:var(--text);letter-spacing:.1px}
.diamond{position:absolute;width:14px;height:14px;border:2px solid var(--gold);transform:rotate(45deg);opacity:.6}

/* hero */
.hero{top:0;height:509px;background:
  radial-gradient(ellipse 320px 220px at 300px 420px,rgba(90,64,34,.45),transparent 70%),
  radial-gradient(ellipse 260px 200px at 640px 380px,rgba(70,52,30,.5),transparent 70%),
  radial-gradient(ellipse 300px 260px at 1000px 120px,rgba(60,44,26,.5),transparent 70%),
  linear-gradient(120deg,#15110b 0%,#0c0a07 45%,#14100a 75%,#090807 100%)}
.brand-mark{left:96px;top:42px;width:140px;text-align:center;font-family:"Bitter",serif;font-weight:600;color:var(--gold);font-size:24px;line-height:30px}
.nav a{position:absolute;top:34px;font-family:"Bitter",serif;font-size:19px;color:#e9e9e9;text-decoration:none}
.nav .star{position:absolute;left:516px;top:64px}
.hero-kicker{left:99px;top:176px;font-family:"Bitter",serif;font-size:46px;color:var(--white);font-weight:400}
.hero-title{left:97px;top:235px;font-family:"Bitter",serif;font-weight:700;font-size:108px;color:var(--gold);letter-spacing:2px;line-height:120px}
.hero-photo{left:780px;top:144px;width:332px;height:365px;background:
  radial-gradient(ellipse 70px 90px at 190px 70px,#8a6a55 0%,#5a4032 60%,transparent 100%),
  radial-gradient(ellipse 80px 70px at 190px 150px,#3a2a22 0%,transparent 100%),
  radial-gradient(ellipse 170px 140px at 190px 300px,#3a4558 0%,#232a36 60%,transparent 100%),
  radial-gradient(ellipse 60px 200px at 40px 120px,rgba(200,148,22,.85),transparent 100%),
  linear-gradient(180deg,#1c1813 0%,#17161a 100%)}
.slide-tag{left:1140px;top:178px;writing-mode:vertical-rl;color:var(--gold);font-size:17px;font-family:"Josefin Sans",sans-serif}

/* about */
.about{top:509px;height:654px;background:var(--coal)}
/* shop */
.shop{top:1163px;height:700px;background:var(--black)}
.shop-card-img{position:absolute;background:#0d0d0d}
.shop-label{position:absolute;top:580px;width:288px;text-align:center;font-family:"Bitter",serif;font-weight:500;font-size:34px;color:var(--gold)}
/* why */
.why{top:1863px;height:657px;background:var(--coal)}
/* gallery */
.gallery{top:2520px;height:733px;background:var(--black)}
.tile{position:absolute}
/* faq */
.faq{top:3253px;height:633px;background:var(--coal)}
.faq-box{position:absolute;background:var(--white);border-radius:8px;color:var(--dark-text);font-size:15px;line-height:25px;text-transform:uppercase;padding:14px 20px 10px 50px;letter-spacing:.3px}
.faq-box.open{background:var(--gold);color:var(--white)}
.faq-num{position:absolute;width:60px;height:60px;border-radius:50%;background:var(--gold);color:var(--white);font-family:"Josefin Sans",sans-serif;font-weight:600;font-size:30px;display:flex;align-items:center;justify-content:center;padding-top:4px}
.faq-num.active{background:var(--black)}
/* footer */
.footer{top:3886px;height:346px;background:
  radial-gradient(ellipse 300px 160px at 300px 120px,rgba(60,52,44,.45),transparent 70%),
  radial-gradient(ellipse 300px 160px at 900px 160px,rgba(55,48,40,.45),transparent 70%),
  linear-gradient(180deg,#0b0b0b 0%,#151311 50%,#0e0d0c 100%)}
.footer-mark{left:0;top:95px;width:1200px;text-align:center;font-family:"Bitter",serif;font-weight:600;font-size:40px;line-height:48px;color:var(--white)}
.contact-icon{position:absolute;width:37px;height:37px;border-radius:50%;background:var(--gold);display:flex;align-items:center;justify-content:center}
.contact-label{position:absolute;font-size:12.5px;color:var(--gold);text-transform:uppercase}
.contact-value{position:absolute;font-family:"Roboto",sans-serif;font-size:14px;color:var(--white);line-height:22px}
.foot-nav{top:4232px;height:68px;background:var(--gold)}
.foot-nav a{position:absolute;top:22px;font-family:"Bitter",serif;font-weight:500;font-size:17px;color:var(--dark-text);text-decoration:none}
.copyright{top:4300px;height:70px;background:var(--black);display:flex;align-items:center;justify-content:center;font-family:"Bitter",serif;font-size:15px;font-weight:500;color:var(--white)}
</style>
</head>
<body>

<header class="section hero">
  <div class="abs brand-mark">The Gilded<br>Viper</div>
  <nav class="nav">
    <a style="left:503px">About</a>
    <a style="left:634px">FAQ</a>
    <a style="left:758px">Gallery</a>
    <a style="left:900px">Inquiries</a>
    <a style="left:1060px">shop</a>
    <svg class="star" width="16" height="16" viewBox="0 0 16 16"><path d="M8 0L10 6 16 8 10 10 8 16 6 10 0 8 6 6Z" fill="var(--gold)"/></svg>
  </nav>
  <div class="abs hero-kicker">The Gilded</div>
  <div class="abs hero-title">VIPER</div>
  <div class="btn" style="left:105px;top:387px;width:172px;height:51px">Get Started</div>
  <div class="photo hero-photo" role="img" aria-label="Portrait of a bearded tattooed artist with folded arms"></div>
  <svg class="abs" style="left:752px;top:318px" width="14" height="14" viewBox="0 0 16 16"><path d="M8 0L10 6 16 8 10 10 8 16 6 10 0 8 6 6Z" fill="var(--gold)"/></svg>
  <svg class="abs" style="left:1149px;top:178px" width="12" height="24" viewBox="0 0 12 24"><path d="M6 24V2M1 7L6 2 11 7" stroke="var(--gold)" stroke-width="2" fill="none"/></svg>
  <div class="abs slide-tag" style="top:208px">Slide 01/04</div>
</header>

<section class="section about">
  <div class="frame" style="left:166px;top:51px;width:340px;height:482px"></div>
  <div class="photo" style="left:124px;top:78px;width:356px;height:485px;background:
    radial-gradient(ellipse 40px 70px at 150px 110px,#a8241c 0%,#5a1a14 60%,transparent 100%),
    radial-gradient(ellipse 120px 60px at 200px 300px,#b08a5a 0%,#6a4e30 55%,transparent 100%),
    radial-gradient(ellipse 180px 90px at 160px 420px,#d8cfc0 0%,#8a7c6a 50%,transparent 100%),
    radial-gradient(ellipse 200px 150px at 300px 90px,#4a3828 0%,transparent 100%),
    linear-gradient(180deg,#2a2019 0%,#1a1410 50%,#3a3028 100%)" role="img" aria-label="Tattoo machine and ink bottle on a workbench"></div>
  <h2 class="abs heading" style="left:589px;top:92px;font-size:50px">About Us</h2>
  <p class="para" style="left:589px;top:175px;width:478px">Sed ut perspiciatis unde omnis iste natus error sit voluptatem accusantium doloremque laudantium, totam rem aperiam, eaque ipsa quae ab illo inventore veritatis et quasi architecto beatae vitae dicta sunt explicabo. Nemo enim ipsam voluptatem quia voluptas sit aspernatur aut odit aut fugit, sed quia consequuntur magni dolores eos qui ratione voluptatem sequi nesciunt. Neque porro quisquam est, qui dolorem ipsum quia dolor sit amet, consectetur, adipisci velit, sed quia non numquam eius modi tempora incidunt ut labore et dolore magnam aliquam quaerat voluptatem.</p>
  <div class="btn" style="left:592px;top:453px;width:175px;height:56px">Read More</div>
  <div class="diamond" style="left:1039px;top:594px"></div>
</section>

<section class="section shop">
  <h2 class="abs heading" style="left:0;top:70px;width:1200px;text-align:center;font-size:50px">Shop</h2>
  <div class="frame" style="left:119px;top:169px;width:288px;height:370px;border-color:#ddd"></div>
  <div class="shop-card-img" style="left:102px;top:195px;width:288px;height:373px;background:
    radial-gradient(ellipse 95px 115px at 144px 180px,#1c1c1c 0%,#141414 70%,transparent 100%),
    radial-gradient(ellipse 30px 45px at 150px 175px,#bdbdbd 0%,transparent 100%),
    #0c0c0c" role="img" aria-label="Black t-shirt with printed artwork"></div>
  <div class="frame" style="left:467px;top:169px;width:286px;height:370px"></div>
  <div class="shop-card-img" style="left:450px;top:195px;width:288px;height:373px;background:
    radial-gradient(ellipse 50px 40px at 145px 110px,#e8e8e8 0%,transparent 100%),
    radial-gradient(ellipse 55px 45px at 140px 245px,#c8242a 0%,transparent 100%),
    linear-gradient(#0a0a0a,#0a0a0a) center/236px 320px no-repeat,
    linear-gradient(135deg,#d6b24a,#8a6a1c 50%,#c9a23c)" role="img" aria-label="Framed tattoo flash art print"></div>
  <div class="frame" style="left:813px;top:169px;width:287px;height:370px;border-color:#ddd"></div>
  <div class="shop-card-img" style="left:794px;top:195px;width:289px;height:373px;background:
    radial-gradient(ellipse 85px 85px at 130px 185px,#f2f2f2 0%,#d8d8d8 70%,transparent 100%),
    radial-gradient(ellipse 30px 45px at 220px 185px,#cfcfcf 0%,transparent 100%),
    #0c0c0c" role="img" aria-label="White ceramic mug with printed design"></div>
  <div class="shop-label" style="left:102px">T Shirts</div>
  <div class="shop-label" style="left:450px">Tattoo/Art</div>
  <div class="shop-label" style="left:794px">Cups</div>
</section>

<section class="section why">
  <h2 class="abs heading" style="left:119px;top:92px;font-size:50px">Why Choose Us</h2>
  <p class="para" style="left:126px;top:177px;width:478px">Sed ut perspiciatis unde omnis iste natus error sit voluptatem accusantium doloremque laudantium, totam rem aperiam, eaque ipsa quae ab illo inventore veritatis et quasi architecto beatae vitae dicta sunt explicabo. Nemo enim ipsam voluptatem quia voluptas sit aspernatur aut odit aut fugit, sed quia consequuntur magni dolores eos qui ratione voluptatem sequi nesciunt. Neque porro quisquam est, qui dolorem ipsum quia dolor sit amet, consectetur, adipisci velit, sed quia non numquam eius modi tempora incidunt ut labore et dolore magnam aliquam quaerat voluptatem.</p>
  <div class="btn" style="left:129px;top:457px;width:175px;height:54px">Read More</div>
  <div class="frame" style="left:748px;top:55px;width:340px;height:483px"></div>
  <div class="photo" style="left:706px;top:80px;width:356px;height:487px;background:
    radial-gradient(ellipse 130px 90px at 170px 210px,#4f7fb0 0%,#2e5680 55%,transparent 100%),
    radial-gradient(ellipse 120px 110px at 280px 60px,#8a6a5a 0%,transparent 100%),
    radial-gradient(ellipse 220px 120px at 180px 420px,#a07860 0%,#5a4234 60%,transparent 100%),
    radial-gradient(ellipse 40px 90px at 110px 110px,#c8c8c8 0%,transparent 100%),
    linear-gradient(180deg,#2a2522 0%,#1c1916 100%)" role="img" aria-label="Artist in blue gloves tattooing a client's back"></div>
</section>

<section class="section gallery">
  <h2 class="abs heading" style="left:0;top:70px;width:1200px;text-align:center;font-size:50px">Gallery</h2>
  <div class="diamond" style="left:139px;top:104px"></div>
  <div class="tile" style="left:104px;top:166px;width:319px;height:231px;background:
    radial-gradient(ellipse 80px 60px at 260px 100px,#5a4630 0%,transparent 100%),
    radial-gradient(ellipse 90px 50px at 90px 150px,#6a5238 0%,transparent 100%),
    linear-gradient(135deg,#2e2418,#1a150f)" role="img" aria-label="Studio work in progress"></div>
  <div class="tile" style="left:445px;top:166px;width:317px;height:231px;background:
    radial-gradient(ellipse 80px 70px at 200px 100px,#e6e6e6 0%,#9a9a9a 50%,transparent 100%),
    radial-gradient(ellipse 60px 40px at 120px 175px,#d0d0d0 0%,transparent 100%),
    linear-gradient(135deg,#151515,#4a4a4a 60%,#1a1a1a)" role="img" aria-label="Gloved hand holding a tattoo machine"></div>
  <div class="tile" style="left:782px;top:166px;width:319px;height:231px;background:
    radial-gradient(ellipse 120px 80px at 150px 140px,#d8d8d8 0%,#8a8a8a 60%,transparent 100%),
    radial-gradient(ellipse 50px 120px at 270px 80px,#4a4a4a 0%,transparent 100%),
    linear-gradient(135deg,#a0a0a0,#4a4a4a)" role="img" aria-label="Tattoo flash sheet with equipment"></div>
  <div class="tile" style="left:104px;top:419px;width:319px;height:229px;background:
    radial-gradient(ellipse 35px 110px at 135px 120px,#6a6a6a 0%,#3a3a3a 60%,transparent 100%),
    radial-gradient(ellipse 35px 110px at 190px 120px,#6a6a6a 0%,#3a3a3a 60%,transparent 100%),
    linear-gradient(180deg,#2a2a2a,#121212)" role="img" aria-label="Tattooed legs"></div>
  <div class="tile" style="left:445px;top:419px;width:317px;height:229px;background:
    radial-gradient(ellipse 130px 100px at 110px 110px,#f0f0f0 0%,#b8b8b8 50%,transparent 100%),
    radial-gradient(ellipse 90px 80px at 250px 150px,#1a1a1a 0%,transparent 100%),
    linear-gradient(135deg,#8a8a8a,#2a2a2a)" role="img" aria-label="Tattooing a large floral piece"></div>
  <div class="tile" style="left:782px;top:419px;width:319px;height:229px;background:
    radial-gradient(ellipse 40px 90px at 170px 140px,#c8c8c8 0%,#7a7a7a 60%,transparent 100%),
    linear-gradient(180deg,#7a7a7a 0%,#4a4a4a 35%,#262626 100%)" role="img" aria-label="Tattooed person in a field"></div>
</section>

<section class="section faq">
  <h2 class="abs heading" style="left:0;top:70px;width:1200px;text-align:center;font-size:50px">FAQ</h2>

  <div class="faq-box" style="left:92px;top:178px;width:482px;height:87px;padding-top:20px">Sed ut perspiciatis unde omnis iste natus error sit voluptatem accusantium</div>
  <div class="faq-num" style="left:63px;top:192px">01</div>

  <div class="faq-box" style="left:92px;top:280px;width:482px;height:84px;padding-top:20px">Sed ut perspiciatis unde omnis iste natus error sit voluptatem accusantium</div>
  <div class="faq-num" style="left:63px;top:292px">02</div>

  <div class="faq-box open" style="left:92px;top:380px;width:482px;height:160px">Sed ut perspiciatis unde omnis iste natus error sit voluptatem accusantium doloremque laudantium, totam rem aperiam, eaque ipsa quae ab illo inventore veritatis et quasi architecto beatae vitae dicta sunt</div>
  <div class="faq-num active" style="left:63px;top:393px">03</div>

  <div class="faq-box" style="left:647px;top:178px;width:480px;height:87px;padding-top:8px">Sed ut perspiciatis unde omnis iste natus error sit voluptatem accusantium doloremque laudantium, totam rem aperiam,</div>
  <div class="faq-num" style="left:622px;top:192px">04</div>

  <div class="faq-box" style="left:647px;top:280px;width:480px;height:84px;padding-top:18px">Sed ut perspiciatis unde omnis iste natus error sit voluptatem accusantium</div>
  <div class="faq-num" style="left:622px;top:290px">05</div>

  <div class="faq-box" style="left:647px;top:380px;width:480px;height:85px;padding-top:18px">Sed ut perspiciatis unde omnis iste natus error sit voluptatem accusantium</div>
  <div class="faq-num" style="left:622px;top:393px">06</div>
</section>

<footer>
  <div class="section footer" role="img" aria-label="Dim studio scene behind the footer">
    <div class="abs footer-mark">The Gilded<br>Viper</div>

    <div class="contact-icon" style="left:123px;top:272px"><svg width="18" height="14" viewBox="0 0 18 14"><rect x="1" y="1" width="16" height="12" rx="1" fill="none" stroke="#fff" stroke-width="1.6"/><path d="M1 2L9 8 17 2" fill="none" stroke="#fff" stroke-width="1.6"/></svg></div>
    <div class="contact-label" style="left:173px;top:272px">Email</div>
    <div class="contact-value" style="left:176px;top:290px">info@gildedviper.com</div>

    <div class="contact-icon" style="left:454px;top:272px"><svg width="14" height="18" viewBox="0 0 14 18"><path d="M7 17C7 17 1 10 1 6.5A6 6 0 0 1 13 6.5C13 10 7 17 7 17Z" fill="#fff"/><circle cx="7" cy="6.5" r="2.2" fill="var(--gold)"/></svg></div>
    <div class="contact-label" style="left:504px;top:272px">Our Location</div>
    <div class="contact-value" style="left:507px;top:290px;width:160px;font-size:12px;line-height:24px">200 Lorem ipsum dolor sit amet,</div>

    <div class="contact-icon" style="left:812px;top:272px"><svg width="16" height="16" viewBox="0 0 16 16"><path d="M3 1L6 1 7 5 5 6.5C6 9 7 10 9.5 11L11 9 15 10 15 13C15 14 14 15 13 15 6 15 1 10 1 3 1 2 2 1 3 1Z" fill="#fff"/></svg></div>
    <div class="contact-label" style="left:864px;top:272px">Phone Number</div>
    <div class="contact-value" style="left:866px;top:290px">+1 555-014-2290</div>
  </div>

  <nav class="section foot-nav">
    <a style="left:335px">Home</a>
    <a style="left:430px">About</a>
    <a style="left:523px">FAQ</a>
    <a style="left:600px">Gallery</a>
    <a style="left:705px">Inquiries</a>
    <a style="left:823px">Shop</a>
  </nav>
  <div class="section copyright">Copyright © 2023 The Gilded Viper - All Rights Reserved.</div>
</footer>

</body>
</html>
```